Retail Sign for Houseplant Campaign

Sign will measure 3 to 4 foot tall by 22.2inches and place on rolling racks of houseplants for a retail promotion in The Birchwell Yard. The theme of the promotion will be "New Year, New You!" Selling points which should be on the sign are Houseplants give you a taste of nature, Houseplants boost air quality inside your home, Indoor plants reduce anxiety, Indoor plants make you more productive, Houseplants improve your concentration and memory.
Updates

Target Market(s)

People who love plants

Industry/Entity Type

Horticulture/ retail

Colors
00AB8E
00BBA5
67D7C9
C6EFE9
E9F9F6
59FF00
82FF00
B8FF75
E3FFCB
F4FFEA
FFF300
FFF600
FEFA6F
FFFEC7
FFFEE8

Requirements
Must have
• Must feel energetic and encourage people to buy plants. Should include 1-2 photos and the selling points listed

```html
<!DOCTYPE html>
<html lang="en">
<head>
<meta charset="utf-8">
<title>New Year, New You! – The Birchwell Yard Houseplant Sign</title>
<link rel="stylesheet" href="https://fonts.googleapis.com/css2?family=Damion&family=Comic+Neue:wght@400;700&display=swap">
<style>
  :root {
    --stage: #c9c9c9;
    --sign-yellow: #fff244;
    --ink: #232323;
    --teal: #67d7c9;
    --lime: #59ff00;
    --pale-lime: #b8ff75;
    --leaf-pale: #cfe04a;
    --leaf-deep: #7fa83c;
    --photo-light: #e6ece9;
    --photo-warm: #c9a98c;
  }
  * { margin: 0; padding: 0; box-sizing: border-box; }
  html, body {
    width: 717px;
    height: 1200px;
    overflow: hidden;
    background: var(--stage);
  }
  .sign {
    position: absolute;
    left: 90px;
    top: 20px;
    width: 537px;
    height: 1160px;
    background: var(--sign-yellow);
    overflow: hidden;
  }
  .decor { position: absolute; left: 0; top: 0; width: 537px; height: 1160px; }
  .headline {
    position: absolute;
    left: 0;
    top: 52px;
    width: 537px;
    text-align: center;
    font-family: "Damion", cursive;
    font-weight: 400;
    font-size: 92px;
    line-height: 100px;
    color: var(--ink);
  }
  .headline span { display: block; }
  .selling-points {
    position: absolute;
    left: 0;
    top: 276px;
    width: 537px;
    list-style: none;
    text-align: center;
    font-family: "Comic Neue", cursive;
    font-size: 23px;
    line-height: 34px;
    color: var(--ink);
  }
  .selling-points li { margin-bottom: 14px; }
</style>
</head>
<body>
  <main class="sign">
    <svg class="decor" viewBox="0 0 537 1160" xmlns="http://www.w3.org/2000/svg">
      <path role="img" aria-label="Pale monstera leaf photo" fill="var(--leaf-pale)" opacity="0.85"
        d="M0 0 H170 C205 40 210 110 185 160 C160 195 100 205 60 190 C30 180 10 170 0 160 Z"/>
      <path role="img" aria-label="Green monstera leaf photo" fill="var(--leaf-deep)"
        d="M537 0 V115 C500 120 455 110 437 85 C432 55 455 20 480 0 Z"/>
      <path class="wave" fill="var(--teal)"
        d="M0 1068 C40 1045 80 1025 120 1028 C200 1035 260 1110 330 1136 C390 1150 430 1110 470 1112 C500 1114 520 1130 537 1146 V1160 H0 Z"/>
      <circle class="photo-ring" cx="262" cy="859" r="201" fill="none" stroke="var(--ink)" stroke-width="0.8"/>
      <defs>
        <linearGradient id="photoTone" x1="0" y1="0" x2="1" y2="1">
          <stop offset="0" stop-color="var(--photo-light)"/>
          <stop offset="1" stop-color="var(--photo-warm)"/>
        </linearGradient>
      </defs>
      <circle role="img" aria-label="Photo of a woman placing a potted croton plant on a shelf"
        cx="262" cy="859" r="185" fill="url(#photoTone)"/>
      <circle class="accent-dot" cx="425" cy="741" r="28" fill="var(--lime)"/>
      <circle class="accent-dot" cx="94" cy="960" r="28" fill="var(--pale-lime)"/>
    </svg>

    <h1 class="headline"><span>New Year,</span><span>New You!</span></h1>

    <ul class="selling-points">
      <li>Houseplants give you a<br>taste of nature</li>
      <li>Houseplants boost air quality<br>inside your home</li>
      <li>Indoor plants reduce anxiety</li>
      <li>Indoor plants make you<br>more productive</li>
      <li>Houseplants improve your<br>concentration and memory</li>
    </ul>
  </main>
</body>
</html>
```